Bright and beautiful business card for a coach

I'm a personal and business coach based in Perth, Australia. I need a business card that whilst subtle and elegant, will stand out and appeal on a table full of cards.

My business name is Fern Mentoring and the business card must represent the warmth and brightness implied in the name, without being gimmicky. It must have a warmth and appeal and be easy to read.

I prefer clean, minimalist designs.

It must align with the feel of my website and socials: https://www.fernmentoring-example.com.au/
https://www.instagram.com/fernmentoringau/
https://www.facebook.com/fernmentoringau
Updates

Hi Designers Thank you so much for taking the time to submit designs. I wonder if I could have explained myself a little better. Most of the designs that have been submitted look rather formal and many have quite corporate looking embellishments on them (to my eye). I would like softer, warmer, more organic. I’m open to people playing about and being more abstract, using softer embellishments (e.g the line drawing flowers and grasses I’ve used in my socials) incorporating other colours from my palette or like the social icons in my email signature (in PDF), perhaps playing with size/oversize, playing with the bleed. Please don’t be constrained by what I’ve already done, it merely needs to compliment. I’m sorry if I’m not using the right words or have led you astray. I’m no designer, but I’ve done my website, socials, email signature etc all myself (my logo was a design contest) and I was really hoping for my business card to be something more creative than I could have made with a template. Reminder: No black cards/sides please. Thank you 😊

Target Market(s)

Individuals, most likely but not all female. Creative thinkers. Likely professionals.

Industry/Entity Type

Business & Personal Coach

Contact Information for Business Card

(Fern Mentoring Logo) Name: Greta Pellham; Title: Business & Personal Coach; Phone number: +61 (0)458 913307; Email: greta@fernmentoring-example.com.au; Website: https://fernmentoring-example.com.au; Social icons for Facebook, Instagram & LinkedIn: @fernmentoringAU. Optional strapline: "A thinking partner to help you cut through the noise"

Font styles to use
Sans Serif

Colors
00AB8E
00BBA5
67D7C9
C6EFE9
E9F9F6
59FF00
82FF00
B8FF75
E3FFCB
F4FFEA
FFC000
F8CF3A
FAE287
FDF2CF
FEFAEE

Requirements
Must have
• Must align with feel of my website and socials. Must have a pop of #FFC000 (possibly whole of one side, or at least a block). Bright or white background. Easy to read.
Nice to have
• Possibly incorporate the sunshine/grass picture I have used in website and socials - will upload.
Should not have
• Must not be black or dark. Not impersonal or corporate looking.

```html
<!DOCTYPE html>
<html lang="en">
<head>
<meta charset="utf-8">
<title>Fern Mentoring – Business Card</title>
<link rel="stylesheet" href="https://fonts.googleapis.com/css2?family=Source+Sans+3:wght@300;400;600;700&display=swap">
<style>
  :root {
    --sun-yellow: #F4B711;
    --ink-grey: #666a6e;
    --paper: #ffffff;
    --canvas-bg: #f1efe9;
    --photo-light: #fff6d6;
    --photo-gold: #e9c45a;
    --photo-green: #7f9a2f;
    --photo-deep: #4f6420;
  }
  * { box-sizing: border-box; margin: 0; padding: 0; }
  html, body {
    width: 1200px; height: 1200px; overflow: hidden;
    background: var(--canvas-bg);
    font-family: "Source Sans 3", sans-serif;
  }
  .canvas {
    width: 1200px; height: 1200px;
    display: flex; flex-direction: column; align-items: center; justify-content: center;
    gap: 56px;
  }
  .card {
    position: relative;
    width: 900px; height: 512px;
    border-radius: 27px;
    overflow: hidden;
    box-shadow: 0 6px 22px rgba(0,0,0,0.12);
  }

  /* Front */
  .card-front { background: var(--paper); }
  .holder { position: absolute; left: 76px; top: 120px; }
  .holder-name {
    color: var(--sun-yellow); font-weight: 700; font-size: 42px; line-height: 1;
  }
  .holder-title {
    color: var(--ink-grey); font-weight: 300; font-size: 27px; margin-top: 6px;
  }
  .brand {
    position: absolute; right: 70px; top: 128px;
    display: flex; align-items: center; gap: 14px;
    color: var(--sun-yellow); font-weight: 400; font-size: 40px; letter-spacing: 0.5px;
  }
  .brand-dot { width: 18px; height: 18px; border-radius: 50%; background: var(--sun-yellow); }
  .contacts {
    position: absolute; left: 76px; top: 322px;
    list-style: none; display: flex; flex-direction: column; gap: 14px;
  }
  .contact-row {
    display: flex; align-items: center; gap: 14px;
    color: var(--ink-grey); font-weight: 300; font-size: 26px; line-height: 30px;
  }
  .icon {
    width: 28px; height: 28px; border-radius: 50%; background: var(--sun-yellow);
    display: flex; align-items: center; justify-content: center; flex: none;
  }
  .social-icons { display: flex; gap: 4px; margin-right: 2px; }
  .website {
    position: absolute; right: 69px; top: 409px;
    color: var(--ink-grey); font-weight: 300; font-size: 26px;
  }
  .accent-bar {
    position: absolute; left: 545px; width: 285px; bottom: 0; height: 25px;
    background: var(--sun-yellow);
  }

  /* Back */
  .card-back {
    background:
      radial-gradient(circle at 62% 12%, var(--photo-light) 0, rgba(255,240,190,0.85) 60px, rgba(233,196,90,0.5) 170px, rgba(233,196,90,0) 330px),
      radial-gradient(ellipse at 15% 30%, rgba(110,140,40,0.8) 0, rgba(110,140,40,0) 300px),
      linear-gradient(180deg, #a79a4e 0%, var(--photo-green) 45%, #8aa83a 70%, var(--photo-deep) 100%);
  }
  .back-photo { position: absolute; inset: 0; }
  .back-brand {
    position: absolute; left: 86px; top: 222px; width: 410px;
    text-align: center; color: var(--paper); font-weight: 400; font-size: 46px; letter-spacing: 1px;
  }
  .strapline {
    position: absolute; left: 170px; width: 322px; top: 384px;
    text-align: center; color: var(--paper); font-weight: 600; font-size: 22px; line-height: 27px;
  }
</style>
</head>
<body>
<main class="canvas">

  <section class="card card-front" aria-label="Business card front">
    <div class="holder">
      <h1 class="holder-name">Greta Pellham</h1>
      <p class="holder-title">Business &amp; Personal Coach</p>
    </div>

    <div class="brand"><span class="brand-dot"></span>Fern Mentoring</div>

    <ul class="contacts">
      <li class="contact-row">
        <span class="icon">
          <svg width="16" height="16" viewBox="0 0 24 24" aria-hidden="true"><path fill="#fff" d="M6.6 10.8a15.1 15.1 0 0 0 6.6 6.6l2.2-2.2a1 1 0 0 1 1-.25 11.4 11.4 0 0 0 3.6.57 1 1 0 0 1 1 1V20a1 1 0 0 1-1 1A17 17 0 0 1 3 4a1 1 0 0 1 1-1h3.5a1 1 0 0 1 1 1c0 1.25.2 2.45.57 3.57a1 1 0 0 1-.25 1z"/></svg>
        </span>
        +61 (0)458 913307
      </li>
      <li class="contact-row">
        <span class="icon">
          <svg width="16" height="16" viewBox="0 0 24 24" aria-hidden="true"><rect x="3" y="6" width="18" height="13" rx="2" fill="none" stroke="#fff" stroke-width="2"/><path d="M3.5 7l8.5 6 8.5-6" fill="none" stroke="#fff" stroke-width="2"/></svg>
        </span>
        greta@fernmentoring-example.com.au
      </li>
      <li class="contact-row">
        <span class="social-icons">
          <span class="icon"></span><span class="icon"></span><span class="icon"></span>
        </span>
        @fernmentoringAU
      </li>
    </ul>

    <p class="website">www.fernmentoring-example.com.au</p>
    <div class="accent-bar"></div>
  </section>

  <section class="card card-back" aria-label="Business card back">
    <div class="back-photo" role="img" aria-label="Sunlit grass meadow photograph with a glowing sun and a white line drawing of a flower on the right"></div>
    <p class="back-brand">Fern Mentoring</p>
    <p class="strapline">“A Thinking Partner To Help You Cut Through The Noise”</p>
  </section>

</main>
</body>
</html>
```